Verlindo Magician

I want the business card for my business to give to people who watch that later I will be employed to show magic here is my website http://www.balsamomagicien.com/I want the interesting design , i am very opened for formal and informal, I watch a lot of design so don't stick to the common shape and form but i hope it can also be produced the thing to write on will be the same as in picture that i will upload , i also will upload the logo for you that so can be easy to useDenis CostilleMagicianMAGICIAN BALSAMO 17 rue des Tilleuls - 25000 BESANÇON contact@verlindoillusions.example tel. 0381 946 157 tel. 0674 219 503

```html
<!DOCTYPE html>
<html lang="fr">
<head>
<meta charset="utf-8">
<title>Verlindo Magician – Business Card</title>
<link href="https://fonts.googleapis.com/css2?family=Open+Sans:wght@300;400;700&display=swap" rel="stylesheet">
<style>
  :root {
    --page: #ececec;
    --card: #ffffff;
    --ink: #1a1a1a;
    --red: #d3312b;
    --black: #0d0d0d;
    --portrait: #2a2a2a;
    --portrait-light: #6b6b6b;
  }
  * { margin: 0; padding: 0; box-sizing: border-box; }
  html, body { width: 1200px; height: 900px; overflow: hidden; }
  body {
    background: var(--page);
    font-family: "Open Sans", Arial, sans-serif;
    color: var(--ink);
    position: relative;
  }
  .card {
    position: absolute;
    left: 280px;
    width: 640px;
    height: 366px;
    background: var(--card);
    box-shadow: 0 4px 18px rgba(0,0,0,0.15);
    overflow: hidden;
  }
  .card--front { top: 62px; }
  .card--back { top: 472px; }

  /* front */
  .front__portrait {
    position: absolute;
    left: 245px; top: 46px;
    width: 150px; height: 170px;
    border-radius: 40px 40px 8px 8px;
    background: linear-gradient(180deg, var(--portrait-light), var(--portrait));
  }
  .front__name {
    position: absolute;
    left: 0; right: 0; top: 226px;
    text-align: center;
    font-weight: 300;
    font-size: 40px;
    letter-spacing: 3px;
    color: var(--ink);
  }

  /* back */
  .back__swoosh { position: absolute; inset: 0; }
  .back__portrait {
    position: absolute;
    left: 430px; top: 26px;
    width: 140px; height: 150px;
    border-radius: 40px 40px 8px 8px;
    background: linear-gradient(180deg, var(--portrait-light), var(--portrait));
  }
  .contact {
    position: absolute;
    left: 46px; top: 62px;
  }
  .contact__name {
    color: var(--red);
    font-weight: 700;
    font-size: 21px;
    line-height: 1.1;
    text-transform: uppercase;
  }
  .contact__role { font-size: 14px; margin: 2px 0 10px 14px; }
  .contact__list { list-style: none; margin-left: 14px; }
  .contact__item {
    display: flex; align-items: center; gap: 7px;
    font-size: 15px; line-height: 21px;
  }
  .contact__icon { width: 13px; height: 13px; flex: none; }
  .contact__company {
    color: var(--red);
    font-weight: 700;
    font-size: 16px;
    margin: 6px 0 0 14px;
    text-transform: uppercase;
  }
  .contact__address { font-size: 15px; line-height: 20px; margin-left: 14px; }
</style>
</head>
<body>

<section class="card card--front" aria-label="Card front">
  <div class="front__portrait" role="img" aria-label="Black and white illustration of the magician holding a playing card"></div>
  <div class="front__name">VERLINDO</div>
</section>

<section class="card card--back" aria-label="Card back">
  <svg class="back__swoosh" viewBox="0 0 640 366" preserveAspectRatio="none" aria-hidden="true">
    <path d="M0 366 L0 342 C 210 336, 410 250, 640 160 L640 366 Z" fill="var(--black)"/>
    <path d="M0 326 C 220 322, 420 232, 600 166 C 430 240, 220 332, 0 336 Z" fill="var(--red)"/>
  </svg>
  <div class="back__portrait" role="img" aria-label="Black and white illustration of the magician holding a playing card"></div>

  <div class="contact">
    <h1 class="contact__name">Marc Ravoulet</h1>
    <p class="contact__role">Magician</p>
    <ul class="contact__list">
      <li class="contact__item">
        <svg class="contact__icon" viewBox="0 0 16 16"><path d="M1 6 C1 3 4 2 8 2 C12 2 15 3 15 6 L11 7 L10 5 H6 L5 7 Z M3 9 H13 V14 H3 Z" fill="var(--red)"/></svg>
        0381 946 157
      </li>
      <li class="contact__item">
        <svg class="contact__icon" viewBox="0 0 16 16"><path d="M1 6 C1 3 4 2 8 2 C12 2 15 3 15 6 L11 7 L10 5 H6 L5 7 Z M3 9 H13 V14 H3 Z" fill="var(--red)"/></svg>
        0674 219 503
      </li>
      <li class="contact__item">
        <svg class="contact__icon" viewBox="0 0 16 16"><rect x="1" y="3" width="14" height="10" fill="var(--red)"/><path d="M1 3 L8 9 L15 3" stroke="#fff" stroke-width="1.4" fill="none"/></svg>
        contact@verlindoillusions.example
      </li>
      <li class="contact__item">
        <svg class="contact__icon" viewBox="0 0 16 16"><circle cx="8" cy="8" r="7" fill="var(--red)"/><path d="M1 8 H15 M8 1 C5 4 5 12 8 15 C11 12 11 4 8 1" stroke="#fff" stroke-width="1" fill="none"/></svg>
        www.verlindoillusions.example
      </li>
    </ul>
    <p class="contact__company">Magician Verlindo</p>
    <p class="contact__address">17 rue des Tilleuls - 25000<br>BESANÇON</p>
  </div>
</section>

</body>
</html>
```